Business Card Design

We are a Sydney based bespoke Concierge company, providing hospitality services including Concierge staffing, catering, home dining, events, delivery, stagequill, and manage desks in residential apartment services. Our website goes into more detail.

Target Market(s)

corporate clients, upscale residential clients, executives,

Industry/Entity Type

Hospitality

Contact Information for Business Card

David SouthwellDirector of Operations & Customer Experience
Larkmere Concierge
W:www.larkmereconcierge.net;
E;marcus@larkmereconcierge.net
M: 0471 295 803

Font styles to use
Serif

Colors
3176b5
85cae6
d2a4cc
6b449b

Requirements
Must have
• Business name
• Name
• Title
• Tel
• Email
• Website
Nice to have
• Back - facebook , twitter, instagram

```html
<!DOCTYPE html>
<html lang="en">
<head>
<meta charset="utf-8">
<title>Larkmere Concierge – Business Card</title>
<link rel="stylesheet" href="https://fonts.googleapis.com/css2?family=Open+Sans:wght@400;600;700&display=swap">
<style>
  :root {
    --backdrop: #ece8e2;
    --card: #ffffff;
    --ink: #333333;
    --black: #000000;
    --stripe: #8a8a8a;
    --blue-deep: #0a3a8f;
    --blue-mid: #1466c4;
    --blue-light: #1ea6e6;
    --bullet: #1e8fd6;
    --white: #ffffff;
  }
  * { box-sizing: border-box; margin: 0; padding: 0; }
  html, body {
    width: 983px; height: 1200px; overflow: hidden;
    background: var(--backdrop);
    font-family: "Open Sans", Arial, sans-serif;
    color: var(--ink);
  }
  .canvas { position: relative; width: 983px; height: 1200px; }
  .card {
    position: absolute; width: 784px; height: 468px;
    background: var(--card); overflow: hidden;
    box-shadow: 0 2px 6px rgba(0,0,0,.18);
  }
  .card--back { left: 99px; top: 75px; }
  .card--front { left: 90px; top: 622px; }
  .card__header { position: absolute; left: 0; top: 0; display: block; }

  .wordmark {
    position: absolute; color: var(--white); font-weight: 400;
    text-transform: uppercase; line-height: 1;
  }
  .card--back .wordmark { left: 184px; top: 44px; font-size: 60px; line-height: 57px; letter-spacing: .5px; }
  .card--front .wordmark { left: 95px; top: 64px; font-size: 39px; line-height: 37px; }

  .web-banner {
    position: absolute; left: 189px; top: 190px;
    color: var(--white); font-weight: 700; font-size: 30px;
  }
  .services { position: absolute; left: 190px; top: 250px; font-size: 24px; }
  .services__title { font-weight: 700; margin-bottom: 4px; }
  .services__list { list-style: none; }
  .services__list li { line-height: 39px; }
  .services__list li::before { content: "•"; color: var(--bullet); margin-right: 8px; }

  .person { position: absolute; left: 96px; top: 213px; color: var(--white); }
  .person__name { font-size: 28px; font-weight: 700; line-height: 38px; }
  .person__title { font-size: 19px; font-weight: 400; margin-top: 6px; }

  .contacts { position: absolute; left: 96px; top: 310px; list-style: none; font-size: 27px; }
  .contacts li { display: flex; align-items: center; height: 42px; }
  .contacts svg { width: 26px; height: 26px; margin-right: 12px; flex: none; }
</style>
</head>
<body>
<main class="canvas">

  <section class="card card--back">
    <svg class="card__header" width="784" height="237" viewBox="0 0 784 237">
      <defs>
        <linearGradient id="bandBack" x1="0" y1="0" x2="0" y2="1">
          <stop offset="0" stop-color="#1a72cf"/>
          <stop offset="1" stop-color="#0a56b3"/>
        </linearGradient>
      </defs>
      <rect x="0" y="139" width="784" height="98" fill="url(#bandBack)"/>
      <path d="M0,0 H784 V192 H200 C110,192 25,170 0,80 Z" fill="var(--stripe)"/>
      <path d="M0,0 H784 V183 H200 C105,183 22,160 0,70 Z" fill="var(--black)"/>
    </svg>
    <div class="wordmark">Larkmere<br>Concierge</div>
    <div class="web-banner">www.larkmereconcierge.net</div>
    <div class="services">
      <p class="services__title">Specializing in:</p>
      <ul class="services__list">
        <li>Event planning</li>
        <li>Apartment concierge services</li>
        <li>Retail centre management and corporate</li>
        <li>Lifestyle and personal concierge services</li>
      </ul>
    </div>
  </section>

  <section class="card card--front">
    <svg class="card__header" width="784" height="290" viewBox="0 0 784 290">
      <defs>
        <linearGradient id="bandFront" x1="0" y1="0" x2="0" y2="1">
          <stop offset="0" stop-color="var(--blue-light)"/>
          <stop offset=".45" stop-color="var(--blue-mid)"/>
          <stop offset="1" stop-color="var(--blue-deep)"/>
        </linearGradient>
      </defs>
      <rect x="0" y="150" width="784" height="140" fill="url(#bandFront)"/>
      <path d="M0,0 H784 V101 C765,185 690,205 590,205 H0 Z" fill="var(--stripe)"/>
      <path d="M0,0 H784 V93 C762,175 685,196 590,196 H0 Z" fill="var(--black)"/>
    </svg>
    <div class="wordmark">Larkmere<br>Concierge</div>
    <div class="person">
      <p class="person__name">Marcus Pendleby</p>
      <p class="person__title">Director of Operations &amp; Customer Experience</p>
    </div>
    <ul class="contacts">
      <li>
        <svg viewBox="0 0 26 26" aria-hidden="true"><rect x="2" y="7" width="22" height="14" rx="1.5" fill="none" stroke="#1b5fae" stroke-width="2"/><path d="M3 8 L13 15 L23 8" fill="none" stroke="#1b5fae" stroke-width="2"/></svg>
        marcus@larkmereconcierge.net
      </li>
      <li>
        <svg viewBox="0 0 26 26" aria-hidden="true"><rect x="7" y="2" width="12" height="22" rx="2" fill="none" stroke="#1b5fae" stroke-width="2"/><rect x="9" y="5" width="8" height="13" fill="#7cc6ee"/><circle cx="13" cy="21" r="1" fill="#1b5fae"/></svg>
        0471 295 803
      </li>
      <li>
        <svg viewBox="0 0 26 26" aria-hidden="true"><circle cx="13" cy="13" r="10" fill="none" stroke="#1b5fae" stroke-width="2"/><ellipse cx="13" cy="13" rx="4.5" ry="10" fill="none" stroke="#1b5fae" stroke-width="1.5"/><path d="M3 13 H23 M5 8 H21 M5 18 H21" stroke="#1b5fae" stroke-width="1.5"/></svg>
        www.larkmereconcierge.net
      </li>
    </ul>
  </section>

</main>
</body>
</html>
```